Business Cards for Internet Security Company

Awesome designers! This is the opportunity to help design cards for a forward thinking network security company. They use threat information gathered from peer groups to make intelligent decisions on what threats are relevant and which arent. ( not that you need this to do designs, but just so you know where they are coming from. ) :-)

We'd like to see a two side design and the deliverables will be in illustrator 4. The logo is attached and the logo colors are attached in the JPG and I've attached a an eps of the logo and icon

Security

```html
<!DOCTYPE html>
<html lang="en">
<head>
<meta charset="utf-8">
<title>Corvane Business Cards</title>
<link rel="stylesheet" href="https://fonts.googleapis.com/css2?family=Didact+Gothic&family=Roboto:wght@400;700&display=swap">
<style>
  :root {
    --page: #eceef1;
    --card: #ffffff;
    --brand: #3a6a9c;
    --brand-dark: #2d5683;
    --brand-light: #4f82b8;
    --ink: #1d2a3a;
    --muted: #2f4e72;
    --rule: #c9ced6;
  }
  * { box-sizing: border-box; margin: 0; padding: 0; }
  html, body { width: 1200px; height: 913px; overflow: hidden; background: var(--page); }
  .canvas { position: relative; width: 1200px; height: 913px; }
  .card {
    position: absolute; left: 250px; width: 700px; height: 400px;
    background: var(--card); overflow: hidden;
    box-shadow: 0 8px 24px rgba(20, 40, 70, 0.18);
  }
  .card--front { top: 38px; }
  .card--back { top: 475px; }
  .wordmark {
    font-family: "Didact Gothic", sans-serif; font-weight: 400;
    color: var(--brand); letter-spacing: 1px; line-height: 1;
    display: flex; align-items: center; gap: 14px;
  }
  .wordmark__dot { border-radius: 50%; background: var(--brand); flex: none; }
  .card--front .wordmark { position: absolute; left: 0; right: 0; top: 138px; justify-content: center; font-size: 92px; }
  .card--front .wordmark__dot { width: 54px; height: 54px; }
  .band { position: absolute; bottom: 0; }
  .card--front .band--main { left: 0; width: 72%; height: 34px; background: var(--brand); }
  .card--front .band--end { right: 0; width: 27%; height: 34px; background: var(--brand-dark); }
  .card--back .wordmark { position: absolute; left: 44px; top: 86px; font-size: 64px; }
  .card--back .wordmark__dot { width: 38px; height: 38px; }
  .rule { position: absolute; left: 44px; top: 168px; width: 612px; height: 1px; background: var(--rule); }
  .contact { position: absolute; left: 400px; top: 196px; list-style: none; font-family: "Roboto", sans-serif; font-size: 15px; color: var(--muted); }
  .contact li { display: flex; align-items: flex-start; gap: 12px; margin-bottom: 7px; line-height: 1.3; }
  .contact svg { width: 16px; height: 16px; flex: none; margin-top: 1px; fill: var(--muted); }
  .person { position: absolute; left: 44px; top: 300px; font-family: "Roboto", sans-serif; }
  .person__name { font-weight: 700; font-size: 21px; color: var(--ink); }
  .person__title { font-size: 16px; color: var(--brand); margin-top: 4px; }
  .card--back .band--left { left: 0; width: 36%; height: 22px; background: linear-gradient(90deg, var(--brand-light), var(--brand)); }
  .card--back .band--right { left: 37.5%; right: 0; height: 22px; background: var(--brand-dark); }
</style>
</head>
<body>
<main class="canvas">
  <section class="card card--front" aria-label="Card front">
    <div class="wordmark"><span class="wordmark__dot"></span>Corvane</div>
    <div class="band band--main"></div>
    <div class="band band--end"></div>
  </section>

  <section class="card card--back" aria-label="Card back">
    <div class="wordmark"><span class="wordmark__dot"></span>Corvane</div>
    <div class="rule"></div>
    <ul class="contact">
      <li>
        <svg viewBox="0 0 16 16" aria-hidden="true"><path d="M8 0a5.5 5.5 0 0 0-5.5 5.5C2.5 9.6 8 16 8 16s5.5-6.4 5.5-10.5A5.5 5.5 0 0 0 8 0zm0 7.8a2.3 2.3 0 1 1 0-4.6 2.3 2.3 0 0 1 0 4.6z"/></svg>
        <span>Your Communication Address in<br>just two line</span>
      </li>
      <li>
        <svg viewBox="0 0 16 16" aria-hidden="true"><path d="M3.6 1 6 3.6 4.7 5.6c.9 2.2 3.2 4.6 5.6 5.6l2-1.3L15 12.4l-1.4 2.4C7 15 1 9 1.2 2.4z"/></svg>
        <span>(000) 000-000-000</span>
      </li>
      <li>
        <svg viewBox="0 0 16 16" aria-hidden="true"><path d="M1 3h14v10H1zm1.5 1.2L8 8.6l5.5-4.4z"/></svg>
        <span>yourname@yourwebsite.com</span>
      </li>
      <li>
        <svg viewBox="0 0 16 16" aria-hidden="true"><path d="M8 1a7 7 0 1 0 0 14A7 7 0 0 0 8 1zm5.4 6.3h-2.6a11 11 0 0 0-.9-4.5 5.6 5.6 0 0 1 3.5 4.5zM8 2.5c.7.9 1.3 2.6 1.4 4.8H6.6C6.7 5.1 7.3 3.4 8 2.5zM6.1 2.8a11 11 0 0 0-.9 4.5H2.6a5.6 5.6 0 0 1 3.5-4.5zM2.6 8.7h2.6a11 11 0 0 0 .9 4.5 5.6 5.6 0 0 1-3.5-4.5zM8 13.5c-.7-.9-1.3-2.6-1.4-4.8h2.8c-.1 2.2-.7 3.9-1.4 4.8zm1.9-.3a11 11 0 0 0 .9-4.5h2.6a5.6 5.6 0 0 1-3.5 4.5z"/></svg>
        <span>www.yourwebsite.com</span>
      </li>
    </ul>
    <div class="person">
      <p class="person__name">Your Name</p>
      <p class="person__title">Title</p>
    </div>
    <div class="band band--left"></div>
    <div class="band band--right"></div>
  </section>
</main>
</body>
</html>
```